Brindle Asset Management Vendor Recruiting Email

We need a digital flyer to email and post on Social media to attract new vendors to our website to apply to complete maintenance work on our clients homes. I have one flyer we had produced recently that we are un-happy with. It is attached.

The example given is what we do not want!! We do not want any of the pictures used from the existing one

Target Market(s)

Construction companies and handyman

Industry/Entity Type

Residential maintenance and repairs

Requirements
Must have
• Join our team as the header not become a vendor

```html
<!DOCTYPE html>
<html lang="en">
<head>
<meta charset="utf-8">
<title>Brindle Asset Management – Join Our Team</title>
<link rel="stylesheet" href="https://fonts.googleapis.com/css2?family=Bebas+Neue&family=Oswald:wght@400&family=Poppins:wght@400;500;600;700;800&display=swap">
<style>
  :root{
    --plum-deep:#24132f;
    --plum:#3a1f45;
    --orchid:#9c5ea7;
    --slate-violet:#666596;
    --ink:#14111d;
    --azure:#0a72bc;
    --indigo:#2d2e8a;
    --white:#ffffff;
    --text-dark:#1b1b22;
    --sky:#4fa9e0;
  }
  *{margin:0;padding:0;box-sizing:border-box}
  html,body{width:966px;height:1200px;overflow:hidden;background:#f1f0f5}
  .flyer{position:relative;width:966px;height:1200px;overflow:hidden;background:var(--white);font-family:'Poppins',sans-serif;color:var(--text-dark)}
  .backdrop{position:absolute;inset:0}
  .abs{position:absolute}
  .brand{left:56px;top:100px;width:200px;color:var(--white);font-family:'Poppins',sans-serif;font-weight:600;text-align:center;line-height:1}
  .brand-mark{display:block;width:40px;height:40px;background:var(--white);margin:0 auto 20px}
  .brand-name{display:block;font-size:25px;letter-spacing:4px}
  .brand-sub{display:block;font-size:9.5px;letter-spacing:2.2px;margin-top:7px}
  .headline{font-family:'Bebas Neue',sans-serif;color:var(--white);line-height:1}
  .headline-top{left:49px;top:243px;font-size:118px;letter-spacing:9px}
  .headline-main{left:50px;top:334px;font-size:252px;letter-spacing:14px}
  .req-title{left:87px;top:560px;font-family:'Bebas Neue',sans-serif;color:var(--white);font-size:54px;letter-spacing:2.5px;line-height:1}
  .req-sub{left:87px;top:607px;font-family:'Bebas Neue',sans-serif;color:var(--white);font-size:34px;letter-spacing:9.5px;line-height:1}
  .checklist{list-style:none;font-size:15.5px;line-height:1.22;color:var(--text-dark)}
  .checklist li{position:absolute;padding-left:23px;white-space:nowrap}
  .checklist svg{position:absolute;left:0;top:4px;width:13px;height:13px}
  .stat{position:absolute;color:var(--white)}
  .stat-approval{left:63px;top:819px;width:267px;height:118px;background:var(--slate-violet)}
  .stat-approval .ring{position:absolute;left:26px;top:34px;width:42px;height:42px}
  .stat-approval .big{position:absolute;left:93px;top:18px;font-weight:700;font-size:52px;line-height:1}
  .stat-approval .note{position:absolute;left:93px;top:77px;font-size:12.5px;line-height:1.25}
  .stat-approval .note b{font-weight:700}
  .stat-volume{left:341px;top:819px;width:380px;height:118px}
  .stat-volume .line1{position:absolute;left:18px;top:20px;font-weight:600;font-size:30px;line-height:1}
  .stat-volume .line2{position:absolute;left:17px;top:56px;font-weight:700;font-size:40px;line-height:1}
  .stat-volume .layers{position:absolute;left:231px;top:14px;width:56px;height:46px}
  .stat-material{left:63px;top:948px;width:267px;height:119px;background:var(--azure)}
  .stat-material .icon{position:absolute;left:17px;top:40px;width:56px;height:56px}
  .stat-material .title{position:absolute;left:93px;top:8px;font-weight:700;font-size:23px;line-height:1.02}
  .stat-material .note{position:absolute;left:93px;top:83px;font-size:10.5px;line-height:1.25}
  .stat-deposit{left:341px;top:948px;width:445px;height:119px}
  .stat-deposit .icon{position:absolute;left:14px;top:36px;width:72px;height:52px}
  .stat-deposit .title{position:absolute;left:117px;top:10px;font-weight:700;font-size:31px;line-height:1.15}
  .stat-deposit .note{position:absolute;left:117px;top:86px;font-size:17.5px;line-height:1}
  .call{left:67px;top:1085px;display:flex;align-items:center;white-space:nowrap}
  .call svg{width:22px;height:22px;margin-right:11px}
  .call-label{font-family:'Bebas Neue',sans-serif;font-size:40px;letter-spacing:4px;color:var(--text-dark);line-height:1;margin-right:14px}
  .call-number{font-family:'Poppins',sans-serif;font-weight:800;font-size:44px;letter-spacing:2px;color:var(--text-dark);line-height:1}
  .rule{left:67px;top:1133px;width:592px;height:1px;background:#555}
  .web{left:67px;top:1138px;display:flex;align-items:center;white-space:nowrap}
  .web svg{width:22px;height:22px;margin-right:11px}
  .web span{font-family:'Oswald',sans-serif;font-weight:400;font-size:30px;letter-spacing:5.4px;color:var(--text-dark);line-height:1.2}
</style>
</head>
<body>
<div class="flyer">

  <svg class="backdrop" width="966" height="1200" viewBox="0 0 966 1200">
    <defs>
      <linearGradient id="plumFade" x1="0" y1="0" x2="0" y2="1">
        <stop offset="0" stop-color="#24132f"/>
        <stop offset="0.75" stop-color="#2e1839"/>
        <stop offset="0.88" stop-color="#7d4a8e"/>
        <stop offset="1" stop-color="#ffffff"/>
      </linearGradient>
      <linearGradient id="photoTone" x1="0" y1="0" x2="0.4" y2="1">
        <stop offset="0" stop-color="#b8dcd2"/>
        <stop offset="0.25" stop-color="#c9a46a"/>
        <stop offset="0.45" stop-color="#a075b5"/>
        <stop offset="0.65" stop-color="#3b4c86"/>
        <stop offset="0.85" stop-color="#c88a5a"/>
        <stop offset="1" stop-color="#e9e4e2"/>
      </linearGradient>
      <linearGradient id="edgeStrip" x1="0" y1="0" x2="1" y2="0">
        <stop offset="0" stop-color="#9c5ea7"/>
        <stop offset="0.5" stop-color="#7f7fbf"/>
        <stop offset="1" stop-color="#4fa9e0"/>
      </linearGradient>
    </defs>
    <rect x="0" y="0" width="966" height="760" fill="url(#plumFade)"/>
    <polygon role="img" aria-label="Photo of a smiling tradesman in a hard hat holding a power drill on a job site"
      points="229,0 966,0 966,1200 864,1200 649,795" fill="url(#photoTone)"/>
    <polygon points="539,0 778,0 666,252" fill="var(--plum-deep)"/>
    <polygon points="63,549 525,549 578,653 63,653" fill="var(--orchid)"/>
    <polygon points="0,653 578,653 649,795 0,795" fill="#ffffff"/>
    <polygon points="341,819 653,819 717,937 341,937" fill="var(--ink)"/>
    <polygon points="341,948 740,948 783,1067 341,1067" fill="var(--indigo)"/>
    <rect x="0" y="1186" width="860" height="14" fill="url(#edgeStrip)"/>
  </svg>

  <div class="abs brand">
    <span class="brand-mark"></span>
    <span class="brand-name">BRINDLE</span>
    <span class="brand-sub">ASSET MANAGEMENT</span>
  </div>

  <div class="abs headline headline-top">JOIN OUR</div>
  <div class="abs headline headline-main">TEAM</div>

  <div class="abs req-title">REQUIREMENTS</div>
  <div class="abs req-sub">TO BECOME A VENDOR</div>

  <ul class="checklist">
    <li style="left:95px;top:670px"><svg viewBox="0 0 14 14"><path d="M1 7.5l4 4L13 3" fill="none" stroke="#1b1b22" stroke-width="2.2"/></svg>Auto insurance</li>
    <li style="left:95px;top:708px"><svg viewBox="0 0 14 14" style="top:13px"><path d="M1 7.5l4 4L13 3" fill="none" stroke="#1b1b22" stroke-width="2.2"/></svg>Certificate of<br>general liability<br>insurance</li>
    <li style="left:95px;top:776px"><svg viewBox="0 0 14 14"><path d="M1 7.5l4 4L13 3" fill="none" stroke="#1b1b22" stroke-width="2.2"/></svg>Coverage area</li>
    <li style="left:278px;top:668px"><svg viewBox="0 0 14 14" style="top:7px"><path d="M1 7.5l4 4L13 3" fill="none" stroke="#1b1b22" stroke-width="2.2"/></svg>Workman’s compensation or<br>state issued exemption letter</li>
    <li style="left:278px;top:722px"><svg viewBox="0 0 14 14" style="top:9px"><path d="M1 7.5l4 4L13 3" fill="none" stroke="#1b1b22" stroke-width="2.2"/></svg>Drive licence or state issued<br>ID card</li>
    <li style="left:278px;top:778px"><svg viewBox="0 0 14 14"><path d="M1 7.5l4 4L13 3" fill="none" stroke="#1b1b22" stroke-width="2.2"/></svg>Any specialty licenses</li>
  </ul>

  <div class="stat stat-approval">
    <svg class="ring" viewBox="0 0 42 42"><circle cx="21" cy="21" r="19" fill="none" stroke="#fff" stroke-width="2.5"/><path d="M13 21.5l5.5 5.5L29 16" fill="none" stroke="#fff" stroke-width="2.5"/></svg>
    <div class="big">95%</div>
    <div class="note"><b>approval rating</b> on all<br>submitted estimates.</div>
  </div>

  <div class="stat stat-volume">
    <div class="line1">Guaranteed</div>
    <svg class="layers" viewBox="0 0 56 46"><g fill="none" stroke="#fff" stroke-width="2.6" stroke-linejoin="round"><path d="M28 3L52 14 28 25 4 14z"/><path d="M8 21L4 23l24 11 24-11-4-2"/><path d="M8 30l-4 2 24 11 24-11-4-2"/></g></svg>
    <div class="line2">Work Volume.</div>
  </div>

  <div class="stat stat-material">
    <svg class="icon" viewBox="0 0 56 56"><g fill="none" stroke="#fff" stroke-width="2.2"><path d="M10 48V12q0-4 4-4h18l6 6v8"/><rect x="22" y="22" width="30" height="32" rx="3"/><rect x="27" y="27" width="20" height="6"/><rect x="27" y="38" width="4" height="4"/><rect x="34" y="38" width="4" height="4"/><rect x="41" y="38" width="4" height="12"/><rect x="27" y="46" width="4" height="4"/><rect x="34" y="46" width="4" height="4"/></g></svg>
    <div class="title">Material<br>Purchasing<br>Program</div>
    <div class="note">to help vendors with low<br>capital or no or bad credit.</div>
  </div>

  <div class="stat stat-deposit">
    <svg class="icon" viewBox="0 0 72 52"><g fill="none" stroke="#fff" stroke-width="2.4"><rect x="30" y="3" width="38" height="46" rx="2"/><rect x="36" y="9" width="26" height="34"/><circle cx="49" cy="24" r="5"/><path d="M4 18h14l10-6 10 6M4 18v26h10M38 40l-10 4H14"/><circle cx="9" cy="38" r="1.5" fill="#fff"/></g></svg>
    <div class="title">Weekly Secure<br>Direct Deposit</div>
    <div class="note">with net 30 payment terms.</div>
  </div>

  <div class="abs call">
    <svg viewBox="0 0 24 24"><path d="M6.6 10.8a15 15 0 006.6 6.6l2.2-2.2c.3-.3.7-.4 1-.2 1.1.4 2.3.6 3.6.6.6 0 1 .4 1 1V20c0 .6-.4 1-1 1A17 17 0 013 4c0-.6.4-1 1-1h3.5c.6 0 1 .4 1 1 0 1.3.2 2.5.6 3.6.1.3 0 .7-.2 1z" fill="#1b1b22"/></svg>
    <span class="call-label">CALL US NOW!</span>
    <span class="call-number">555-014-2817</span>
  </div>
  <div class="abs rule"></div>
  <div class="abs web">
    <svg viewBox="0 0 24 24"><g fill="none" stroke="#1b1b22" stroke-width="1.5"><circle cx="12" cy="12" r="10"/><ellipse cx="12" cy="12" rx="4.5" ry="10"/><path d="M2 12h20M4 6.5h16M4 17.5h16"/></g></svg>
    <span>www.brindleassetmanagement.com</span>
  </div>

</div>
</body>
</html>
```